real esate business card with company logo and name

we need a business card design for a real esate company

The company name is Walsh & Brand Pty Ltd, and we have our logo designed and will upload. We want classic or moden feel. Black or white background. looks more textured. Should include folowinginformations
Owen Walsh and Lucy Brand
Sales Agents & Onsite Manager
p: 07 5948 2063
F: 07 5948 2174
M:0431 857 219
3/42 Marlow Crescent, FERNLEA QLD 4213

We want this business card looks professonal. Thank you in advance.

Industry/Entity Type

Real Estate Agent

Contact Information for Business Card

Owen Walsh and Lucy Brand
Onsite Manager & Sales Agents
p: 07 5948 2063
M:0431 857 219

Font styles to use
Serif

Colors
000000
fbfbfb
333333
959595

Requirements
Must have
• company logo and name, black or white back ground

```html
<!DOCTYPE html>
<html lang="en">
<head>
<meta charset="utf-8">
<title>Walsh &amp; Brand Pty Ltd — Business Card</title>
<link href="https://fonts.googleapis.com/css2?family=Montserrat:wght@400;500;700&display=swap" rel="stylesheet">
<style>
  :root {
    --black: #000000;
    --paper: #fbfbfb;
    --charcoal: #333333;
    --grey: #959595;
    --backdrop: #1c1c1c;
  }
  * { margin: 0; padding: 0; box-sizing: border-box; }
  html, body {
    width: 1200px;
    height: 800px;
    overflow: hidden;
    background: var(--backdrop);
    font-family: "Montserrat", sans-serif;
  }
  .business-card {
    position: absolute;
    left: 180px;
    top: 160px;
    width: 840px;
    height: 480px;
    background: var(--paper);
    box-shadow: 0 12px 40px rgba(0, 0, 0, 0.5);
    overflow: hidden;
  }
  .card-shapes {
    position: absolute;
    inset: 0;
  }
  .brand {
    position: absolute;
    left: 600px;
    top: 96px;
    display: flex;
    align-items: center;
    gap: 14px;
  }
  .brand-mark {
    width: 34px;
    height: 34px;
    background: var(--charcoal);
  }
  .brand-name {
    font-size: 15px;
    font-weight: 500;
    letter-spacing: 0.08em;
    color: var(--charcoal);
    text-transform: uppercase;
  }
  .agent-names {
    position: absolute;
    left: 56px;
    top: 132px;
    color: var(--paper);
  }
  .agent-names .name {
    font-size: 24px;
    font-weight: 700;
    line-height: 1.05;
    text-transform: uppercase;
    letter-spacing: 0.02em;
  }
  .agent-names .role {
    margin-top: 6px;
    font-size: 14px;
    font-weight: 400;
    letter-spacing: 0.02em;
  }
  .contact-row {
    position: absolute;
    left: 66px;
    display: flex;
    align-items: center;
    gap: 22px;
    color: var(--paper);
    font-size: 15px;
    line-height: 1.45;
    letter-spacing: 0.02em;
  }
  .contact-row.phones { top: 236px; }
  .contact-row.address { top: 322px; }
  .contact-icon { width: 20px; height: 20px; flex: none; }
  .divider {
    position: absolute;
    left: 50px;
    top: 308px;
    width: 380px;
    height: 1px;
    background: var(--grey);
  }
</style>
</head>
<body>
  <article class="business-card">
    <svg class="card-shapes" width="840" height="480" viewBox="0 0 840 480" aria-hidden="true">
      <path class="name-tab" d="M0 120 H350 Q385 120 385 150 V215 H0 Z" fill="var(--grey)"/>
      <path class="contact-band" d="M0 215 H385 L470 215 L600 320 V380 H0 Z" fill="var(--charcoal)"/>
      <path class="accent-band" d="M625 265 H840 V320 H600 V290 Q600 265 625 265 Z" fill="var(--grey)"/>
      <path class="accent-strip" d="M690 320 H840 V338 H712 Z" fill="var(--charcoal)"/>
    </svg>

    <div class="brand">
      <span class="brand-mark"></span>
      <span class="brand-name">Walsh &amp; Brand Pty Ltd.</span>
    </div>

    <header class="agent-names">
      <p class="name">Owen Walsh</p>
      <p class="name">&amp; Lucy Brand</p>
      <p class="role">Sales Agents &amp; Onsite Manager</p>
    </header>

    <div class="contact-row phones">
      <svg class="contact-icon" viewBox="0 0 20 20" aria-hidden="true">
        <rect x="4" y="1" width="12" height="18" rx="2" fill="var(--paper)"/>
        <rect x="6" y="3.5" width="8" height="5" fill="var(--charcoal)"/>
        <g fill="var(--charcoal)">
          <rect x="6" y="10.5" width="2" height="2"/><rect x="9" y="10.5" width="2" height="2"/><rect x="12" y="10.5" width="2" height="2"/>
          <rect x="6" y="14" width="2" height="2"/><rect x="9" y="14" width="2" height="2"/><rect x="12" y="14" width="2" height="2"/>
        </g>
      </svg>
      <div>
        <p>P: 07 5948 2063</p>
        <p>F: 07 5948 2174</p>
        <p>M: 0431 857 219</p>
      </div>
    </div>

    <span class="divider"></span>

    <div class="contact-row address">
      <svg class="contact-icon" viewBox="0 0 20 20" aria-hidden="true">
        <path d="M10 2 L19 10 H16 V18 H12 V13 H8 V18 H4 V10 H1 Z" fill="var(--paper)"/>
      </svg>
      <div>
        <p>3/42 Marlow Crescent,</p>
        <p>FERNLEA QLD 4213</p>
      </div>
    </div>
  </article>
</body>
</html>
```